Business card design for holistic health care clinic

We need a double-sided business card design for our holistic health care clinic that integrates our logo design and also its color scheme. My business is called Valmira. It is an integrative medicine clinic. You have already done the logo for me. Please ensure an elegant and upscale design that is not cluttered, but still has all the necessary information (please see below for details).

Target Market(s)

Wellness, fitness, rehabilitation for educated, well-traveled open-minded clients who are focused on natural, organic, balanced and preventive healthcare and lifestyle.

Industry/Entity Type

Medical

Contact Information for Business Card

Modern, clean.

Number of Pages Required

1 page

Font styles to use
Serif
Sans Serif

Colors

Designer to choose colors to be used in the design.

Requirements
Must have
• Logo on one side, all other information on the other side.
• Other information should include:
• Tobias Wrenfeld - DOE, CPT, LMT
• 4100 East Marrow Drive
• Austin, TX 78119
• 512 555 0148
• 818 555 0192
• info@ValmiraHealth.example
• t.wrenfeld@ValmiraHealth.example
Nice to have
• Darker background on front - but not totally black - shaded/dark gray.

```html
<!DOCTYPE html>
<html lang="en">
<head>
<meta charset="utf-8">
<title>Valmira – Business Card</title>
<link rel="stylesheet" href="https://fonts.googleapis.com/css2?family=Montserrat:wght@500;700&family=Roboto:wght@400;500&display=swap">
<style>
  :root {
    --canvas-bg: #e9e7e4;
    --card-dark: #2a2a2c;
    --brand-blue: #0a91d0;
    --text-light: #f2f2f2;
    --card-radius: 24px;
  }
  * { box-sizing: border-box; margin: 0; padding: 0; }
  html, body {
    width: 1200px; height: 911px; overflow: hidden;
    background: var(--canvas-bg);
  }
  .canvas {
    position: relative; width: 1200px; height: 911px;
    display: flex; justify-content: center; align-items: center; gap: 90px;
  }
  .card {
    position: relative; width: 330px; height: 560px;
    background: var(--card-dark);
    border-radius: var(--card-radius);
    overflow: hidden;
    box-shadow: 0 10px 30px rgba(0,0,0,.25);
  }

  /* Contact side */
  .contact-block {
    position: absolute; top: 48px; left: 0; right: 0;
    text-align: center;
    font-family: "Roboto", sans-serif;
    color: var(--text-light);
  }
  .icon { display: block; margin: 0 auto 6px; width: 14px; height: 14px; fill: var(--brand-blue); }
  .holder-name {
    font-size: 19px; font-weight: 500; color: var(--brand-blue);
    letter-spacing: .3px; margin-bottom: 14px;
  }
  .holder-name .credentials { font-size: 10px; letter-spacing: .5px; }
  .contact-line { font-size: 14px; line-height: 1.35; margin-bottom: 12px; }
  .contact-line.small { font-size: 13.5px; }
  .wave-band { position: absolute; left: 0; bottom: 0; width: 330px; height: 230px; }
  .band-name {
    position: absolute; left: 0; right: 0; bottom: 70px; text-align: center;
    font-family: "Montserrat", sans-serif; font-weight: 700; font-size: 30px;
    letter-spacing: 3px; color: #ffffff;
  }

  /* Logo side */
  .logo-lockup {
    position: absolute; top: 250px; left: 0; right: 0; text-align: center;
    color: var(--brand-blue); font-family: "Montserrat", sans-serif;
  }
  .brand-name { font-size: 44px; font-weight: 700; letter-spacing: 3px; line-height: 1; }
  .brand-tagline { font-size: 13.5px; font-weight: 500; margin-top: 8px; letter-spacing: .3px; }
  .motto-stripe {
    position: absolute; left: 0; right: 0; bottom: 52px; height: 46px;
    background: var(--brand-blue);
    border-top: 3px solid var(--card-dark);
    box-shadow: 0 -6px 0 var(--brand-blue);
    display: flex; align-items: center; justify-content: center;
    font-family: "Roboto", sans-serif; font-size: 15px; color: #ffffff; letter-spacing: .4px;
  }
</style>
</head>
<body>
<main class="canvas">

  <section class="card card--contact" aria-label="Contact side">
    <div class="contact-block">
      <svg class="icon" viewBox="0 0 14 14" aria-hidden="true"><circle cx="7" cy="4" r="3.2"/><path d="M1 14c0-4 3-6 6-6s6 2 6 6z"/></svg>
      <p class="holder-name">TOBIAS WRENFELD <span class="credentials">- DOE, CPT, LMT</span></p>

      <svg class="icon" viewBox="0 0 14 14" aria-hidden="true"><path d="M7 0a5 5 0 0 0-5 5c0 4 5 9 5 9s5-5 5-9a5 5 0 0 0-5-5zm0 7a2 2 0 1 1 0-4 2 2 0 0 1 0 4z"/></svg>
      <p class="contact-line">4100 East Marrow Drive<br>Austin, TX 78119</p>

      <svg class="icon" viewBox="0 0 14 14" aria-hidden="true"><path d="M3 1l2 0 1.5 3.5-1.7 1.2a8 8 0 0 0 3.5 3.5L9.5 7.5 13 9v2c0 1-1 2-2 2C6 13 1 8 1 3c0-1 1-2 2-2z"/></svg>
      <p class="contact-line">512 555 0148</p>

      <svg class="icon" viewBox="0 0 14 14" aria-hidden="true"><path d="M4 0h6a1 1 0 0 1 1 1v12a1 1 0 0 1-1 1H4a1 1 0 0 1-1-1V1a1 1 0 0 1 1-1zm0.5 1.5v9h5v-9z"/></svg>
      <p class="contact-line">818 555 0192</p>

      <svg class="icon" viewBox="0 0 14 14" aria-hidden="true"><path d="M1 3h12v8H1z M1 3l6 5 6-5" stroke="#2a2a2c" stroke-width=".8"/></svg>
      <p class="contact-line small">t.wrenfeld@ValmiraHealth.example</p>

      <svg class="icon" viewBox="0 0 14 14" aria-hidden="true"><circle cx="7" cy="7" r="6.5"/><path d="M.5 7h13M7 .5c-3 3-3 10 0 13M7 .5c3 3 3 10 0 13" stroke="#2a2a2c" stroke-width=".9" fill="none"/></svg>
      <p class="contact-line small">www.ValmiraHealth.example</p>
    </div>

    <svg class="wave-band" viewBox="0 0 330 230" aria-hidden="true">
      <path d="M0 20 C60 10 90 95 170 100 C240 104 290 120 330 130 L330 230 L0 230 Z" fill="#0a91d0"/>
    </svg>
    <p class="band-name">VALMIRA</p>
  </section>

  <section class="card card--logo" aria-label="Logo side">
    <div class="logo-lockup">
      <p class="brand-name">VALMIRA</p>
      <p class="brand-tagline">Integrative Holistic Medicine</p>
    </div>
    <p class="motto-stripe">helping the body help itself</p>
  </section>

</main>
</body>
</html>
```